Online Shop Maren

We need a web design for an online shop, called "Lirvo Dune Jewels". The shop should have an extraordinary, elegant look, as shown in the Quellwick Advertising Picture in our Briefing.pdf (attached). Please have a look at our Briefing regarding website colours, background ideas, and elements to be included. The online shop is about professional jewellery design pieces, where each piece is handmade of high quality materials, also unique pieces and unique editions possible. It should attract extraordinary people and visualize that its a very individual and unique design jewellery. You can get an idea of whom it should attract by reading our target group. Colours to be used are jewellery-Velvet red, Black / anthracite, exclusive colours, silverish-white, bronze-brown and golden.

Please play around when designing with the image pictures we attach, preferably more vertical pictures, no panoramic pictures like in Brovenka Shop. Also include the BLACK logo of lirvo dune. We include the SITEMAP in the briefing and also another folder with product pictures you can use for the draft.

Regarding Functions, the store will have the SAME (technical) functions as this page:http://www.brovenka-shop.eu/ - using the "most famous" products/categories for the starting page, going into individual product pages by clicking these images and then leading to a detailed page for one product only.

Target Market(s)

Jewellery-lovers, who appreciate extraordinary things, creative economy/fashion-industries, stylists, Style consultants, outfitter, theatres, operas, production sites, Cocktail-, Dinner and Bridefashion, exclusive traditional costume stores, dancesports and tango argento dancers

Industry/Entity Type

Shop

Requirements
Must have
• Must include:
• Colours as per briefing
• Background ideas/images as per briefing/pictures sent
• Sitemap as per briefing
• Social buttons
• Logo
• Design for 3 pages: Starting page showing big images, attractive design and the 4 popular categories
• Subpage with different products of one category (i.e. bracelets)
• Detail page with one individual product only
Should not have
• no fresh, playful colours like yellow, orange, green, blue
• no cheap design, no panorama pictures

```html
<!DOCTYPE html>
<html lang="en">
<head>
<meta charset="utf-8">
<title>Lirvo Dune Jewels</title>
<link rel="stylesheet" href="https://fonts.googleapis.com/css2?family=Open+Sans:wght@300;400;600&family=Yesteryear&display=swap">
<style>
:root{
  --velvet:#9b1b1f;
  --velvet-dark:#7d1216;
  --band:rgba(140,38,44,.82);
  --anthracite:#2f2e33;
  --ink:#1c1c1c;
  --paper:#f6f4ef;
  --line:#e3dfd8;
  --muted:#7a7a7a;
  --wood:#4a2a1c;
}
*{box-sizing:border-box;margin:0;padding:0}
html,body{width:923px;height:1200px;overflow:hidden}
body{position:relative;font-family:"Open Sans",Arial,sans-serif;background:var(--paper);color:var(--ink)}

/* header */
.site-header{position:absolute;left:0;top:0;width:923px;height:111px;background:#fff}
.brand{position:absolute;left:84px;top:32px;font-size:35px;font-weight:400;color:var(--ink);letter-spacing:.3px;line-height:1}
.brand-sub{position:absolute;left:136px;top:83px;font-size:18px;color:var(--ink);line-height:1}
.social{position:absolute;left:775px;top:54px;display:flex;gap:5px}
.social span{width:18px;height:18px;border-radius:3px;background:var(--velvet)}
.social span:nth-child(2){background:var(--anthracite)}
.social span:nth-child(3){background:#8a7b6a}
.cart{position:absolute;left:728px;top:85px;font-size:8px;display:flex;align-items:center;gap:4px;white-space:nowrap}
.cart b{font-weight:600}
.cart em{font-style:normal;color:var(--muted)}

/* nav */
.main-nav{position:absolute;left:0;top:111px;width:923px;height:39px;background:linear-gradient(#3a393d,#1f1e22);border-top:1px solid #111}
.main-nav a{position:absolute;top:0;height:38px;line-height:38px;color:#e8e8e8;font-size:12px;text-decoration:none;font-weight:300}
.main-nav a.active{background:var(--velvet);color:#fff;padding:0 12px;left:86px}
.search{position:absolute;left:638px;top:8px;width:196px;height:23px;background:#fff;border:1px solid #ccc;font-size:8.5px;color:#666;line-height:21px;padding-left:8px}
.search svg{position:absolute;right:6px;top:5px}

/* hero */
.hero{position:absolute;left:0;top:150px;width:923px;height:375px;background:linear-gradient(90deg,#3a1f14,var(--wood) 4%,#5b3322 8%,#3d2217 11%,#4a2a1c 100%)}
.hero-photo{position:absolute;left:86px;top:0;width:752px;height:375px;background:linear-gradient(100deg,#f4f2ef 0%,#ebe7e2 45%,#d8b49a 70%,#c9a187 78%,#ece7e1 100%)}
.hero-band{position:absolute;top:349px;height:121px;background:var(--band)}
.hero-band.prev{left:37px;width:79px}
.hero-band.main{left:118px;width:672px}
.hero-band.next{left:793px;width:79px}
.hero-band svg{position:absolute;top:26px}
.tagline-small{position:absolute;left:135px;top:368px;font-family:"Yesteryear",cursive;font-size:27px;color:#fff;line-height:1;white-space:nowrap}
.tagline-big{position:absolute;left:136px;top:393px;font-family:"Yesteryear",cursive;font-size:43px;color:#fff;line-height:1;white-space:nowrap}
.welcome{position:absolute;left:405px;top:360px;font-size:17.5px;line-height:24px;color:#fff;font-weight:400;white-space:nowrap}
.welcome-text{position:absolute;left:408px;top:389px;width:350px;font-size:9.6px;line-height:16.5px;color:#f6e6e6;font-weight:300}
.btn-read{position:absolute;left:410px;top:432px;width:88px;height:27px;background:#fff;border:2px solid #d8d0d0;font-size:10.5px;color:#555;text-align:center;line-height:23px}

/* categories */
.section-title{position:absolute;font-size:21px;font-weight:400;color:var(--ink);white-space:nowrap}
.section-title span{color:#c8191f}
.cat{position:absolute;left:88px;width:156px;height:32px;background:#fff;border:1px solid var(--line)}
.cat p{position:absolute;left:6px;top:8px;font-size:10px;color:#777}
.cat .go{position:absolute;right:-1px;top:-1px;width:39px;height:32px;background:var(--velvet);clip-path:polygon(12% 0,100% 0,100% 100%,12% 100%,0 50%)}
.cat .go svg{position:absolute;left:12px;top:6px}

.offer{position:absolute;left:87px;top:864px;width:159px;height:237px;background:linear-gradient(160deg,#b7a8a6 0%,#8f7c7c 35%,#5a4d4b 70%,#3e3533 100%)}
.offer-box{position:absolute;left:8px;top:87px;width:141px;height:74px;background:rgba(0,0,0,.8);text-align:center;color:#fff;font-size:18.5px;line-height:22px;padding-top:2px;font-weight:400;white-space:nowrap}
.offer-box .red{color:#e01e25}
.btn-shop{position:absolute;left:36px;top:168px;width:87px;height:25px;background:#fff;font-size:8px;color:#333;text-align:center;line-height:21px;border:2px solid #ddd}
.offer-line{position:absolute;left:87px;top:1108px;width:159px;height:3px;background:#d0191f}

/* products */
.card{position:absolute;width:169px;height:169px;background:#fff;border:1px solid var(--line)}
.card .photo{position:absolute;left:7px;top:7px;width:154px;height:154px}
.price{position:absolute;font-size:12.5px;color:var(--velvet)}
.desc{position:absolute;font-size:7px;color:#333;white-space:nowrap}
.btn-cart{position:absolute;width:22px;height:21px;background:var(--velvet)}
.btn-cart svg{position:absolute;left:4px;top:4px}
.btn-info{position:absolute;height:21px;width:79px;background:var(--velvet);color:#fff;font-size:11px;text-align:center;line-height:21px;white-space:nowrap}

.site-footer{position:absolute;left:0;top:1148px;width:923px;height:52px;background:var(--anthracite);color:#ddd;font-size:8px;text-align:center;line-height:52px}
</style>
</head>
<body>

<header class="site-header">
  <div class="brand">Lirvo Dune</div>
  <div class="brand-sub">♦ Jewels ♦</div>
  <div class="social" aria-label="Social links"><span></span><span></span><span></span></div>
  <div class="cart">
    <svg width="13" height="11" viewBox="0 0 13 11"><path d="M0 1h2l2 6h7l1.5-4.5H3" fill="none" stroke="#222" stroke-width="1.2"/><circle cx="5" cy="9.5" r="1" fill="#222"/><circle cx="10" cy="9.5" r="1" fill="#222"/></svg>
    <b>Shopping Cart :</b><em>0 item</em>
  </div>
</header>

<nav class="main-nav">
  <a class="active" href="#">Home</a>
  <a href="#" style="left:161px">Online Shop</a>
  <a href="#" style="left:257px">Info &amp; Facts</a>
  <a href="#" style="left:350px">Partner</a>
  <a href="#" style="left:418px">About me</a>
  <a href="#" style="left:501px">Contact</a>
  <div class="search">Enter your search here...
    <svg width="12" height="12" viewBox="0 0 12 12"><circle cx="5" cy="5" r="3.6" fill="none" stroke="#9b1b1f" stroke-width="1.8"/><path d="M7.6 7.6l3 3" stroke="#9b1b1f" stroke-width="2"/></svg>
  </div>
</nav>

<section class="hero">
  <div class="hero-photo" role="img" aria-label="Model with an upswept hairstyle wearing a long crystal drop earring"></div>
</section>
<div class="hero-band prev"><svg width="40" height="70" viewBox="0 0 40 70" style="left:17px"><path d="M36 2L4 35l32 33" fill="none" stroke="rgba(255,255,255,.75)" stroke-width="2.5"/></svg></div>
<div class="hero-band main"></div>
<div class="hero-band next"><svg width="40" height="70" viewBox="0 0 40 70" style="left:22px"><path d="M4 2l32 33L4 68" fill="none" stroke="rgba(255,255,255,.75)" stroke-width="2.5"/></svg></div>
<div class="tagline-small">Collection 2014</div>
<div class="tagline-big">Designer Jewelry</div>
<h1 class="welcome">Welcome to Lirvo Dune</h1>
<p class="welcome-text">On sait depuis longtemps que travailler avec du texte lisible et contenant du sens est source de distractions, et empêche de se concentrer sur la</p>
<div class="btn-read">READ MORE</div>

<h2 class="section-title" style="left:88px;top:572px">Our <span>Categories</span></h2>
<div class="cat" style="top:621px"><p>Lorem Ipsum</p><div class="go"><svg width="20" height="20" viewBox="0 0 20 20"><circle cx="10" cy="10" r="8.5" fill="none" stroke="#fff" stroke-width="1.6"/><path d="M5.5 10h8M10.5 6.5L14 10l-3.5 3.5" fill="none" stroke="#fff" stroke-width="1.8"/></svg></div></div>
<div class="cat" style="top:659px"><p>Lorem Ipsum</p><div class="go"><svg width="20" height="20" viewBox="0 0 20 20"><circle cx="10" cy="10" r="8.5" fill="none" stroke="#fff" stroke-width="1.6"/><path d="M5.5 10h8M10.5 6.5L14 10l-3.5 3.5" fill="none" stroke="#fff" stroke-width="1.8"/></svg></div></div>
<div class="cat" style="top:697px"><p>Lorem Ipsum</p><div class="go"><svg width="20" height="20" viewBox="0 0 20 20"><circle cx="10" cy="10" r="8.5" fill="none" stroke="#fff" stroke-width="1.6"/><path d="M5.5 10h8M10.5 6.5L14 10l-3.5 3.5" fill="none" stroke="#fff" stroke-width="1.8"/></svg></div></div>
<div class="cat" style="top:735px"><p>Lorem Ipsum</p><div class="go"><svg width="20" height="20" viewBox="0 0 20 20"><circle cx="10" cy="10" r="8.5" fill="none" stroke="#fff" stroke-width="1.6"/><path d="M5.5 10h8M10.5 6.5L14 10l-3.5 3.5" fill="none" stroke="#fff" stroke-width="1.8"/></svg></div></div>
<div class="cat" style="top:774px"><p>Lorem Ipsum</p><div class="go"><svg width="20" height="20" viewBox="0 0 20 20"><circle cx="10" cy="10" r="8.5" fill="none" stroke="#fff" stroke-width="1.6"/><path d="M5.5 10h8M10.5 6.5L14 10l-3.5 3.5" fill="none" stroke="#fff" stroke-width="1.8"/></svg></div></div>
<div class="cat" style="top:812px"><p>Lorem Ipsum</p><div class="go"><svg width="20" height="20" viewBox="0 0 20 20"><circle cx="10" cy="10" r="8.5" fill="none" stroke="#fff" stroke-width="1.6"/><path d="M5.5 10h8M10.5 6.5L14 10l-3.5 3.5" fill="none" stroke="#fff" stroke-width="1.8"/></svg></div></div>

<aside class="offer" role="img" aria-label="Woman in a lace dress standing by a window, promotional offer">
  <div class="offer-box">Special Offer<br>Save<br><span class="red">An Extra 40 %</span></div>
  <div class="btn-shop">SHOP NOW</div>
</aside>
<div class="offer-line"></div>

<h2 class="section-title" style="left:290px;top:573px">Featured <span>Products</span></h2>

<div class="card" style="left:290px;top:619px"><div class="photo" role="img" aria-label="Woman in a flowing gown on garden stairs" style="background:linear-gradient(#5d6550,#7a6a55 50%,#6b5a48)"></div></div>
<div class="card" style="left:477px;top:619px"><div class="photo" role="img" aria-label="Woman in a red dress outdoors" style="background:linear-gradient(135deg,#4e5648,#8a6f5c 45%,#c23a3e 70%,#7c7a62)"></div></div>
<div class="card" style="left:665px;top:619px"><div class="photo" role="img" aria-label="Woman in a white jacket at a balcony" style="background:linear-gradient(135deg,#37475a,#5b6d80 45%,#cfcfd6 75%,#6e7f8e)"></div></div>
<div class="card" style="left:290px;top:879px"><div class="photo" role="img" aria-label="Woman with a lace parasol, back view" style="background:linear-gradient(150deg,#b9cfcf,#8e9c9a 40%,#7a5a50 70%,#c9b8b0)"></div></div>
<div class="card" style="left:477px;top:879px"><div class="photo" role="img" aria-label="Woman wearing a pearl necklace and bracelet" style="background:linear-gradient(120deg,#ddd6d0,#b88a74 45%,#5a3b33 65%,#e6e1dd)"></div></div>
<div class="card" style="left:665px;top:879px"><div class="photo" role="img" aria-label="Woman in a traditional dress by a window" style="background:linear-gradient(135deg,#7d6a72,#a99aa2 45%,#c6bcc6 70%,#8b7d86)"></div></div>

<div class="price" style="left:298px;top:794px">$ 15.00</div>
<div class="price" style="left:483px;top:794px">$ 15.00</div>
<div class="price" style="left:667px;top:794px">$ 15.00</div>
<div class="desc" style="left:300px;top:814px">Contrairement à une opinion répa.</div>
<div class="desc" style="left:486px;top:814px">Contrairement à une opinion répa.</div>
<div class="desc" style="left:674px;top:814px">Contrairement à une opinion répa.</div>

<div class="price" style="left:291px;top:1054px">$ 15.00</div>
<div class="price" style="left:484px;top:1054px">$ 15.00</div>
<div class="price" style="left:669px;top:1054px">$ 15.00</div>
<div class="desc" style="left:297px;top:1075px">Contrairement à une opinion répa.</div>
<div class="desc" style="left:487px;top:1075px">Contrairement à une opinion répa.</div>
<div class="desc" style="left:671px;top:1075px">Contrairement à une opinion répa.</div>

<div class="btn-cart" style="left:301px;top:830px"><svg width="14" height="13" viewBox="0 0 14 13"><path d="M0 1h2.5l2 7h7.5l1.5-5H3.5" fill="none" stroke="#fff" stroke-width="1.6"/><circle cx="5.5" cy="11" r="1.3" fill="#fff"/><circle cx="11" cy="11" r="1.3" fill="#fff"/></svg></div>
<div class="btn-info" style="left:331px;top:830px">Product Info</div>
<div class="btn-cart" style="left:487px;top:830px"><svg width="14" height="13" viewBox="0 0 14 13"><path d="M0 1h2.5l2 7h7.5l1.5-5H3.5" fill="none" stroke="#fff" stroke-width="1.6"/><circle cx="5.5" cy="11" r="1.3" fill="#fff"/><circle cx="11" cy="11" r="1.3" fill="#fff"/></svg></div>
<div class="btn-info" style="left:518px;top:830px">Product Info</div>
<div class="btn-cart" style="left:675px;top:830px"><svg width="14" height="13" viewBox="0 0 14 13"><path d="M0 1h2.5l2 7h7.5l1.5-5H3.5" fill="none" stroke="#fff" stroke-width="1.6"/><circle cx="5.5" cy="11" r="1.3" fill="#fff"/><circle cx="11" cy="11" r="1.3" fill="#fff"/></svg></div>
<div class="btn-info" style="left:705px;top:830px">Product Info</div>

<div class="btn-cart" style="left:299px;top:1091px"><svg width="14" height="13" viewBox="0 0 14 13"><path d="M0 1h2.5l2 7h7.5l1.5-5H3.5" fill="none" stroke="#fff" stroke-width="1.6"/><circle cx="5.5" cy="11" r="1.3" fill="#fff"/><circle cx="11" cy="11" r="1.3" fill="#fff"/></svg></div>
<div class="btn-info" style="left:330px;top:1091px">Product Info</div>
<div class="btn-cart" style="left:487px;top:1091px"><svg width="14" height="13" viewBox="0 0 14 13"><path d="M0 1h2.5l2 7h7.5l1.5-5H3.5" fill="none" stroke="#fff" stroke-width="1.6"/><circle cx="5.5" cy="11" r="1.3" fill="#fff"/><circle cx="11" cy="11" r="1.3" fill="#fff"/></svg></div>
<div class="btn-info" style="left:518px;top:1091px">Product Info</div>
<div class="btn-cart" style="left:673px;top:1091px"><svg width="14" height="13" viewBox="0 0 14 13"><path d="M0 1h2.5l2 7h7.5l1.5-5H3.5" fill="none" stroke="#fff" stroke-width="1.6"/><circle cx="5.5" cy="11" r="1.3" fill="#fff"/><circle cx="11" cy="11" r="1.3" fill="#fff"/></svg></div>
<div class="btn-info" style="left:705px;top:1091px">Product Info</div>

<footer class="site-footer">© Copyrights 2013 All rights Reserved</footer>

</body>
</html>
```